Dorwin and Partners Outpatient Imaging

1. flyer/rack card size, front and back for imaging services advertisement. Color design. Text file and one chest xray and one hand radiograph hopefully. Clean and easy to read. 2. clear to read title about "Outpatient imaging services" 3. Only using images and text provided. This is a radiology group offering web based image interpretation to physicians in the community.

Target Market(s)

Referring outpatient physicians

Industry/Entity Type

Medical Imaging

Font styles to use
Serif

Requirements
Must have
• preferably one picture, easy to read design
Nice to have
• both a hand and chest xray would be nice.

```html
<!DOCTYPE html>
<html lang="en">
<head>
<meta charset="utf-8">
<title>Dorwin and Partners Outpatient Imaging</title>
<link href="https://fonts.googleapis.com/css2?family=Bebas+Neue&family=Lato:wght@400&family=Cormorant+Garamond:wght@500&display=swap" rel="stylesheet">
<style>
  :root {
    --blue-deep: #163452;
    --blue-mid: #2a5f93;
    --blue-light: #3c7fbd;
    --text-white: #ffffff;
    --accent-red: #b3202b;
    --footer-dark: #2a2a2c;
  }
  * { margin: 0; padding: 0; box-sizing: border-box; }
  html, body { width: 1200px; height: 2557px; overflow: hidden; }
  body { font-family: 'Lato', Arial, sans-serif; color: var(--text-white); }
  .rack-card {
    position: relative;
    width: 1200px;
    height: 2557px;
    overflow: hidden;
    background: var(--blue-mid);
  }
  .xray-backdrop {
    position: absolute;
    inset: 0 0 145px 0;
    background:
      radial-gradient(ellipse 60% 40% at 55% 40%, rgba(120,170,220,0.35), transparent 70%),
      linear-gradient(180deg, var(--blue-deep) 0%, var(--blue-mid) 30%, var(--blue-light) 75%, #3a7aba 100%);
  }
  .content { position: absolute; left: 78px; top: 200px; width: 1050px; }
  .body-copy { font-size: 37px; line-height: 48px; }
  .section-title {
    font-family: 'Bebas Neue', Arial Narrow, sans-serif;
    font-size: 76px;
    line-height: 1;
    margin-top: 20px;
    margin-bottom: 10px;
    letter-spacing: 0;
  }
  .headline {
    position: absolute;
    left: 0; right: 0; top: 1320px;
    text-align: center;
    font-family: 'Bebas Neue', Arial Narrow, sans-serif;
    font-size: 112px;
    line-height: 106px;
  }
  .contact {
    position: absolute;
    left: 0; right: 0; top: 1630px;
    text-align: center;
    font-size: 37px;
    line-height: 60px;
  }
  .brand {
    position: absolute;
    left: 170px; top: 2080px;
    width: 870px;
  }
  .brand-name {
    font-family: 'Cormorant Garamond', Georgia, serif;
    font-weight: 500;
    font-size: 64px;
    line-height: 78px;
    padding-left: 68px;
    text-transform: uppercase;
  }
  .brand-rule { height: 3px; background: var(--text-white); margin: 2px 0; }
  .footer-stripe { position: absolute; left: 0; right: 0; top: 2412px; height: 17px; background: var(--accent-red); }
  .footer-band { position: absolute; left: 0; right: 0; top: 2429px; bottom: 0; background: var(--footer-dark); }
</style>
</head>
<body>
<div class="rack-card">
  <div class="xray-backdrop" role="img" aria-label="Faint chest radiograph in blue tones filling the background"></div>

  <div class="content">
    <p class="body-copy">With our dedication to quality patient care, the doctors and staff of Dorwin and Partners go above and beyond to assure your office needs are met. We will work with you through image interpretation, imaging follow-up, and are committed to your confidence in our process. Our goal is to help you integrate our services to create a superior diagnostic and treatment process that works for you and your practice.</p>
    <h2 class="section-title">Our Outpatient Services</h2>
    <p class="body-copy">We identified a need in our communities to provide a better product for our physicians when choosing office based imaging. In 2015 we began working with Veridian Health to provide image interpretation while utilizing state of the art medical data and image management. As a physician owned practice, we pride ourselves on providing high quality and accurate reports with rapid results (a final report within 24 hours). We offer a 24 hour direct phone line for referring physicians to speak with one of our radiologists should a problem arise after hours.</p>
  </div>

  <h1 class="headline">We look forward to being a<br>complete solution for all of<br>your imaging needs.</h1>

  <p class="contact">To hear more about our outpatient services or<br>free in office set up, please contact<br>Dr. Elena Marsh at 517-555-0142.</p>

  <div class="brand">
    <div class="brand-name">Dorwin and</div>
    <div class="brand-rule"></div>
    <div class="brand-name" style="padding-left:10px">Partners, P.C.</div>
  </div>

  <div class="footer-stripe"></div>
  <div class="footer-band"></div>
</div>
</body>
</html>
```